Dentistry Office

We want a new design for a Dentist's office website.

The theme is: "We provide high quality, state-of-the-art, dental care in a comfortable, caring environment."

The site currently has a menu on the left of the page with about 40 items on it. There is a great deal of textual content on each page, plus several illustrations.

We want to do this using CSS, so we need specifications in the CSS for all possible elements. The CSS needs to be named in a logical manner for easy use.

Every dentist on the planet seems to use lots of Flash. We don't want to because it is so distracting. We are looking for an elegant solution targeting 24-55 age group, but not excluding anyone.

The following (from another dentist's site) can give you a taste of what we want to communicate on the site:

"After 20 years of teaching dentists how to refine their technique and many years of writing textbooks, I currently devote my time to my office and the hands-on practice of dentistry. I'd like to welcome you personally to my dental practice, and I invite you to meet my highly experienced team of professionals.

"We have offered complete dental care of the highest quality since 1978. We provide Preventive Services, Tooth Whitening and Cosmetic Dentistry for a beautiful smile, Endodontics (root canal treatment) to treat painful teeth, Sedation Dentistry so you can relax, and Dental Implants to restore what is missing. We offer total care.

"Our approach to your health is simple: We use our education, experience and dedication to provide every patient with superior dental care.

"This passion for excellence is not just a goal, but a standard every member of our team holds.

"We also pride ourselves with our state of the art procedures, training and technology. This includes creating a beautiful smile using techniques that preserve as much of the original tooth as possible.

"Our abilities are renowned throughout the dental profession and I hope if you have any questions you will contact us by an e-mail note, by phone or just by dropping by."

Keep in mind the screen shape and dimensions. Your design needs to work in the normal screen proportions, regardless of how it looks when you post it here. Scrolling is OK, but the first impression needs to work.
Updates

Keep in mind that there will be about 250 words, or more, on each page.

Competitors web sites:

http://www.brindlecovedentist.example/

http://www.brindlecovedentalcare.example/

http://www.grinsbymarlowvaledental.example/

http://www.tenbyfamilydentalcare.example/

http://www.quelmardental.example/

http://www.dovrinadental.example/

We need to compete with these.

Target Market(s)

Generally adults seeking the most experienced and comfortable-to-be-with dentist.

Industry/Entity Type

Training

Requirements
Must have
• Must stand apart from other dentists.
• Must be elegant.
• Must have a horizontal menu structure across all columns, NOT a vertical that requires scrolling, no popout, pop down, etc. menus.
• We are looking for something special.
• Do not waste your time or ours putting up templates and things you have used before.
• Personally, I do not see how someone outside the US can understand the northern California dental market. But you are welcome to try.
Should not have
• Flash or graphics that move
• The look of a template
• Folksy fonts
• Looks like you used it 20 times before

```html
<!DOCTYPE html>
<html lang="en">
<head>
<meta charset="utf-8">
<title>Brindle Cove Dentist — Walter Henning</title>
<link href="https://fonts.googleapis.com/css2?family=Open+Sans:wght@300;400;600;700&family=Arimo:ital,wght@0,400;0,700;1,400;1,700&display=swap" rel="stylesheet">
<style>
:root{
  --side:#b9b9b9;
  --page:#ffffff;
  --slate:#6e7f89;
  --slate-dark:#66757e;
  --slate-light:#8c9ba4;
  --mist:#d3d9dc;
  --ink:#111111;
  --muted:#8a949a;
  --rule:#c9cfd3;
  --bar:#000000;
}
*{margin:0;padding:0;box-sizing:border-box}
html,body{width:923px;height:1200px;overflow:hidden}
body{background:linear-gradient(90deg,#a7a7a7 0,#c9c9c9 41px,#c9c9c9 880px,#a7a7a7 923px);font-family:Arimo,Arial,sans-serif;color:var(--ink)}
.page{position:absolute;left:41px;top:0;width:839px;height:1200px;background:var(--page)}

/* masthead */
.masthead{position:relative;height:212px;background:linear-gradient(90deg,#ececec 0,#f7f7f7 60%,#fff 100%)}
.masthead::before{content:"";position:absolute;left:0;right:0;top:0;height:30px;background:#fff}
.brand{position:absolute;left:23px;top:1px;font-family:"Open Sans",sans-serif;font-weight:400;color:var(--slate);font-size:26px;line-height:30px;letter-spacing:-.3px}
.brand .practice{text-transform:uppercase;display:block}
.brand .doctor{display:block;color:#808b91}
.tagline{position:absolute;left:23px;top:84px;font-family:"Open Sans",sans-serif;font-size:12px;line-height:16.5px;color:#7c878d}
.office-photo{position:absolute;left:501px;top:30px;width:338px;height:182px;background:linear-gradient(160deg,#8a9aa6 0,#6a5446 35%,#4f5a3c 70%,#7f8d5b 100%)}

/* topic directory */
.directory{position:absolute;top:222px;left:0;width:839px;height:156px}
.topic{position:absolute;top:0;font-family:Arimo,Arial,sans-serif}
.topic h3{font-family:"Open Sans",sans-serif;font-weight:400;font-size:13.5px;color:var(--slate);letter-spacing:.2px;margin-bottom:4px}
.topic li{list-style:none;font-size:10px;line-height:13px;color:var(--muted)}
.topic.divided{border-left:1px solid var(--rule);padding-left:17px;min-height:96px}
.t1{left:24px}.t2{left:169px;min-height:156px!important}.t3{left:334px}.t4{left:503px;min-height:126px!important}.t5{left:673px}

/* main menu */
.main-menu{position:absolute;top:388px;left:0;width:839px;height:25px;background:var(--bar)}
.main-menu a{position:absolute;top:0;line-height:25px;color:#fff;font-size:10.5px;font-weight:700;text-decoration:none;letter-spacing:.1px}

/* hero */
.offer{position:absolute;top:413px;left:0;width:168px;height:137px;background:var(--mist);padding:13px 0 0 14px}
.offer h2{font-size:15.5px;line-height:18.5px;font-weight:700;color:var(--slate-light)}
.offer p{font-size:8.5px;line-height:11px;margin-top:5px;color:#000}
.offer p span{display:block;padding-left:9px}
.welcome{position:absolute;top:413px;left:168px;width:671px;height:137px;background:linear-gradient(90deg,#8694a0 0,#7d8c95 45%,#6d7d86 100%);color:#fff;padding:12px 13px}
.welcome h2{font-size:12.5px;font-weight:700;margin-bottom:20px}
.welcome p{font-size:10.8px;line-height:14.8px;margin-bottom:15px}

/* sidebar */
.sidebar{position:absolute;top:550px;left:0;width:168px;height:650px;border-right:1px solid var(--rule);padding:13px 0 0 14px}
.side-heading{font-size:13px;color:var(--slate);font-weight:400;letter-spacing:.2px}
.hours{margin-top:17px;font-size:9.8px;line-height:14.8px}
.hours strong{display:block}
.side-link{display:block;margin-top:18px}
.side-link+.side-link{margin-top:14px}
.contact{position:absolute;left:13px;top:513px;font-size:11px;line-height:14.8px;color:var(--slate-light)}
.contact b{font-size:12.5px;font-weight:700}
.contact p+p{margin-top:16px}

/* content */
.content{position:absolute;top:550px;left:169px;width:670px}
.section{padding:13px 10px 0 20px}
.section h2{font-size:13px;font-weight:400;color:var(--slate);letter-spacing:.2px;margin-bottom:16px}
.services li{list-style:none;font-size:10.7px;line-height:14.8px;padding-left:14px;position:relative}
.services li svg{position:absolute;left:0;top:3px}
.services b{font-weight:700}
.divider{border:0;border-top:1px dashed var(--slate-light);margin:17px 4px 0 2px}
.letter p{font-size:10.7px;line-height:14.8px;margin-bottom:14.8px}
.letter p.ethos{color:var(--slate);font-style:italic;font-weight:700}
</style>
</head>
<body>
<div class="page">

  <header class="masthead">
    <h1 class="brand"><span class="practice">Brindle Cove Dentist</span><span class="doctor">Walter Henning</span></h1>
    <p class="tagline">Providing Cosmetic Dentistry Excellence to Patients in Brindle Cove,<br>Marlow County and the San Francisco Bay Area.</p>
    <div class="office-photo" role="img" aria-label="Photo of the shingled dental office building among garden plants"></div>
  </header>

  <nav class="directory">
    <div class="topic t1"><h3>EDUCATION</h3><ul><li>Emergency Dental Care</li><li>Your Mouth</li><li>Your Tooth</li><li>Cracked Tooth?</li><li>Missing a Tooth?</li><li>Sensitive Teeth</li><li>Dry Mouth</li><li>Tooth Grinding</li><li>Sleep Dentistry</li><li>Videos</li></ul></div>
    <div class="topic divided t2"><h3>PREVENTATIVE</h3><ul><li>What is Preventive Care?</li><li>Taking Care of Your Teeth</li><li>Eating Right</li><li>Dental Check-Ups</li><li>Sealants</li><li>Periodontal Disease</li><li>Kicking the Habit</li><li>Night Guards</li><li>Dental X-Rays</li><li>Antibiotics with Treatment</li></ul></div>
    <div class="topic divided t3"><h3>COSMETICS</h3><ul><li>Cosmetic Dentistry</li><li>Bleaching and Whitening</li><li>Cosmetic Bonding</li><li>Esthetic Veneers</li><li>Tooth Shaping</li></ul></div>
    <div class="topic divided t4"><h3>RESTORATIONS</h3><ul><li>Crowns/Caps: Each Step</li><li>CMBRs</li><li>Porcelain Bridges</li><li>Bonded Dental Bridges</li><li>Gold Restorations</li><li>Implants</li><li>Treating Cracked Teeth</li><li>Periodontal (gum) Treatment</li></ul></div>
    <div class="topic divided t5"><h3>VISITING OUR OFFICE</h3><ul><li>Where to Stay</li><li>First Visit / Map</li><li>Financial Policy</li><li>Dental Insurance</li></ul></div>
  </nav>

  <nav class="main-menu">
    <a href="#" style="left:24px">HOME</a>
    <a href="#" style="left:105px">WHY WE ARE DIFFERENT</a>
    <a href="#" style="left:272px">TECHNOLOGIES WE OFFER</a>
    <a href="#" style="left:451px">MEET DR. HENNING</a>
    <a href="#" style="left:592px">OUR STAFF</a>
    <a href="#" style="left:696px">CONTACT US / LINKS</a>
  </nav>

  <aside class="offer">
    <h2>We offer an Initial Patient Examination, X-rays and Cleaning for $79.00.</h2>
    <p>**New patients only. Offers are<span>cash patients only.&nbsp; Insurance</span><span>will be billed at full value.</span></p>
  </aside>

  <section class="welcome">
    <h2>Located at 2240 Harbor Avenue, Ste E-1, Brindle Cove, CA 95499</h2>
    <p>In Brindle Cove, when you’re a patient of Dr. Henning, you can be confident that you’re receiving care from the most experienced, knowledgeable, and skilled cosmetic dentist in Marlow County.</p>
    <p>Dr. Henning is an award-winning leader in restorative dentistry and a genial professional. His humor, dedication, and talent ensure you a pleasant experience and superb, long-lasting results.</p>
  </section>

  <aside class="sidebar">
    <h2 class="side-heading">OFFICE HOURS</h2>
    <div class="hours"><strong>Our usual office hours are:</strong>Monday 9 am to 6 pm<br>Tuesday 9 am to 5 pm<br>Wednesday 9 am to 5 pm<br>Thursday 9 am to 5 pm<br>Friday 7:30 am to 5 pm</div>
    <a class="side-heading side-link" style="margin-top:31px">MAP TO OFFICE</a>
    <a class="side-heading side-link">WHERE TO STAY?</a>
    <div class="contact">
      <p>Please contact us at<br><b>(707) 555-0142.</b></p>
      <p>To contact us outside office hours for an emergency, please call <b>(707) 555-0188.</b></p>
    </div>
  </aside>

  <main class="content">
    <section class="section">
      <h2>DR. HENNING PROVIDES</h2>
      <ul class="services">
        <li><svg width="9" height="9" viewBox="0 0 10 10"><path d="M5 0L6.2 3.6H10L7 5.9 8.1 9.6 5 7.3 1.9 9.6 3 5.9 0 3.6H3.8Z" fill="#8c9ba4"/></svg><b>General dentistry</b> - oral hygiene, cavity detection and repair, crowns.</li>
        <li><svg width="9" height="9" viewBox="0 0 10 10"><path d="M5 0L6.2 3.6H10L7 5.9 8.1 9.6 5 7.3 1.9 9.6 3 5.9 0 3.6H3.8Z" fill="#8c9ba4"/></svg><b>Cosmetic/restorative dentistry</b> - broken or misshapen teeth, crooked smiles, unsightly gaps</li>
        <li><svg width="9" height="9" viewBox="0 0 10 10"><path d="M5 0L6.2 3.6H10L7 5.9 8.1 9.6 5 7.3 1.9 9.6 3 5.9 0 3.6H3.8Z" fill="#8c9ba4"/></svg><b>Non-metal fillings</b> - nontoxic, durable tooth-colored resin fillings that are proven to provide better results</li>
        <li><svg width="9" height="9" viewBox="0 0 10 10"><path d="M5 0L6.2 3.6H10L7 5.9 8.1 9.6 5 7.3 1.9 9.6 3 5.9 0 3.6H3.8Z" fill="#8c9ba4"/></svg><b>Tooth shaping</b> - extending, shortening or otherwise reshaping teeth for improved esthetics</li>
        <li><svg width="9" height="9" viewBox="0 0 10 10"><path d="M5 0L6.2 3.6H10L7 5.9 8.1 9.6 5 7.3 1.9 9.6 3 5.9 0 3.6H3.8Z" fill="#8c9ba4"/></svg><b>Complete smile make-over's</b> - resin veneers that reshape the whole mouth while preserving natural teeth</li>
        <li><svg width="9" height="9" viewBox="0 0 10 10"><path d="M5 0L6.2 3.6H10L7 5.9 8.1 9.6 5 7.3 1.9 9.6 3 5.9 0 3.6H3.8Z" fill="#8c9ba4"/></svg><b>Tooth whitening</b> - at-home bleaching options to make teeth appear years younger</li>
        <li><svg width="9" height="9" viewBox="0 0 10 10"><path d="M5 0L6.2 3.6H10L7 5.9 8.1 9.6 5 7.3 1.9 9.6 3 5.9 0 3.6H3.8Z" fill="#8c9ba4"/></svg><b>Laser Dentistry, Sleep Dentistry, and Implant Dentistry with the Finest and Latest Equipment and Materials.</b></li>
        <li><svg width="9" height="9" viewBox="0 0 10 10"><path d="M5 0L6.2 3.6H10L7 5.9 8.1 9.6 5 7.3 1.9 9.6 3 5.9 0 3.6H3.8Z" fill="#8c9ba4"/></svg><b>Dental Implants to replace missing teeth.</b></li>
        <li><svg width="9" height="9" viewBox="0 0 10 10"><path d="M5 0L6.2 3.6H10L7 5.9 8.1 9.6 5 7.3 1.9 9.6 3 5.9 0 3.6H3.8Z" fill="#8c9ba4"/></svg><b>Sedation Dentistry so you can be relaxed.</b></li>
      </ul>
    </section>
    <hr class="divider">
    <section class="section letter">
      <h2>DR. HENNING’ COMMITMENT</h2>
      <p>After 25 years of teaching dentists how to refine their technique and many years of writing textbooks, I currently devote my time to my office and the hands-on practice of dentistry. I'd like to welcome you personally to my dental practice, and I invite you to meet my highly experienced team of professionals.</p>
      <p>Dr. Henning and his Associated have offered complete dental care of the highest quality since 1978. We provide Preventive Services, Tooth Whitening and Cosmetic Dentistry for a beautiful smile, Endodontics (root canal treatment) to treat painful teeth, Sedation Dentistry so you can relax, and Dental Implants to restore what is missing. We offer total care.</p>
      <p class="ethos">Our approach to your health is simple: We use our education, experience and dedication to provide every patient with superior dental care.</p>
      <p class="ethos">This passion for excellence is not just a goal, but a standard every member of our team holds.</p>
      <p>We also pride ourselves with our state of the art procedures, training and technology. This includes creating a beautiful smile using techniques that preserve as much of the original tooth as possible.</p>
      <p>Our abilities are renowned throughout the dental profession and I hope if you have any questions you will contact us by an e-mail note, by phone or just by dropping by.</p>
      <p>Thank you.</p>
      <p>Sincerely,</p>
      <p>Walter Henning, DDS FAGD</p>
    </section>
  </main>

</div>
</body>
</html>
```